Brand new letterhead, business card, email signature etc.

We are a financial company in London, UK. Our website is www.marlowvane.com. We're wanting a complete remodel of the company colours, letter head, business cards, email signatures, etc. Looking to keep the same font for the company name. I have upload a colour palette that we want to work with. We're looking for company letterhead for outgoing letters/ correspondence, letterhead for internal documentation, email signatures, e-letters. etc. Ultimately we will redesign the entire website also. It is important that our clients get a strong, secure, warm, trustworthy, solid feeling and first impression.
Updates

Designs look the same

Target Market(s)

Institutional investors, (ultra) high net worth individuals

Industry/Entity Type

Finance, Invesments banking.

Font styles to use
Other font styles liked:
• Current font is "Champagne & Limousines"

Requirements
Must have
• Must use the colours provided on the PDF uploaded to the portal. The purple = main colour. The red = accent colour.
Nice to have
• Nice to use same font as now for the company name "Corvane". Font is "Champagne & Limousines". Nice to have some reference to the old logo flower, but only subtle.
Should not have
• Do not use the colour red from our website. Use the colours provided on the colour palette PDF that I uploaded in the portal.

```html
<!DOCTYPE html>
<html lang="en">
<head>
<meta charset="utf-8">
<title>Corvane Letterhead</title>
<link href="https://fonts.googleapis.com/css2?family=Josefin+Sans:wght@300&family=Urbanist:wght@300;400&display=swap" rel="stylesheet">
<style>
  :root {
    --backdrop: #e8e6e3;
    --paper: #ffffff;
    --ink-strong: #2b2b2b;
    --ink-body: #6f6f6f;
    --ink-soft: #555555;
    --accent-red: #e5451f;
    --band-top: #e64a1e;
    --band-mid: #a2201a;
    --band-low: #6a1419;
    --band-bottom: #2a0119;
    --rule: #3a3a3a;
    --sign-tone: #ececec;
  }
  * { margin: 0; padding: 0; box-sizing: border-box; }
  html, body {
    width: 1200px; height: 900px; overflow: hidden;
    background: var(--backdrop);
  }
  .letterhead {
    position: absolute; left: 296px; top: 20px;
    width: 608px; height: 860px;
    background: var(--paper);
    box-shadow: 0 2px 6px rgba(0,0,0,0.12);
    font-family: "Urbanist", sans-serif;
    color: var(--ink-body);
  }
  .brand-mark {
    position: absolute; left: 58px; top: 48px;
    width: 48px; height: 48px;
    border: 1px solid var(--ink-strong);
  }
  .brand-name {
    position: absolute; left: 119px; top: 58px;
    font-family: "Josefin Sans", sans-serif; font-weight: 300;
    font-size: 29px; letter-spacing: 5px; line-height: 1;
    color: var(--ink-strong); text-transform: uppercase;
  }
  .office-address {
    position: absolute; left: 347px; top: 56px;
    font-size: 9px; line-height: 11px; font-weight: 300;
    color: var(--ink-soft); font-style: normal;
  }
  .contact-divider {
    position: absolute; left: 442px; top: 58px;
    width: 1px; height: 29px; background: var(--rule);
  }
  .contact-list {
    position: absolute; left: 453px; top: 56px;
    list-style: none; font-size: 9px; line-height: 11px;
    font-weight: 300; color: var(--ink-soft);
  }
  .contact-list li { display: flex; align-items: center; gap: 4px; }
  .contact-list svg { width: 6px; height: 6px; fill: var(--accent-red); }
  .side-band {
    position: absolute; left: 58px; top: 103px;
    width: 48px; height: 757px;
    background: linear-gradient(to bottom, var(--band-top) 0%, var(--band-mid) 35%, var(--band-low) 65%, var(--band-bottom) 100%);
  }
  .letter-body {
    position: absolute; left: 130px; top: 230px; width: 438px;
    font-size: 11.4px; line-height: 17.3px; font-weight: 300;
  }
  .letter-date { text-align: right; margin-bottom: 8px; }
  .salutation { margin-bottom: 11px; }
  .letter-body p.para { text-align: justify; margin-bottom: 22px; }
  .letter-body p.para.cut { text-align-last: justify; }
  .letter-body p.para.closing { margin-bottom: 27px; }
  .signature {
    width: 96px; height: 50px; background: var(--sign-tone);
  }
</style>
</head>
<body>
  <main class="letterhead">
    <div class="brand-mark"></div>
    <div class="brand-name">Corvane</div>

    <address class="office-address">
      Office 14/2210<br>
      Harrow Vale Road<br>
      Westbury VIC 3021
    </address>
    <div class="contact-divider"></div>
    <ul class="contact-list">
      <li><svg viewBox="0 0 10 10"><path d="M2 0h2l1 3-1.5 1a6 6 0 0 0 2.5 2.5L7 5l3 1v2c0 1-1 2-2 2A8 8 0 0 1 0 2c0-1 1-2 2-2z"/></svg>1840 31 62 07</li>
      <li><svg viewBox="0 0 10 10"><path d="M0 2h10v6H0z M0 2l5 3.5L10 2" /></svg>contact@marlowvane.com</li>
      <li><svg viewBox="0 0 10 10"><circle cx="5" cy="5" r="5"/></svg>marlowvane.com</li>
    </ul>

    <div class="side-band"></div>

    <section class="letter-body">
      <p class="letter-date">Dated: February 15, 2023</p>
      <p class="salutation">Dear Sir,</p>
      <p class="para cut">Lorem Ipsum is simply dummy text of the printing and typesetting industry. Lorem Ipsum has been the industry's standard dummy text ever since the 1500s, when an unknown printer took a galley of type and scrambled it to make a type specimen book. It has survived not only five centuries, but also the leap into electronic typesetting, remaining essentially unchanged. It was popularised in the 1960s with the release of Letraset sheets containing Lorem Ipsum passages, and more recently</p>
      <p class="para cut">It is a long established fact that a reader will be distracted by the readable content of a page when looking at its layout. The point of using Lorem Ipsum is that it has a more-or-less normal distribution of letters, as opposed to using 'Content here, content here', making it look like readable English. Many desktop publishing packages and web page editors now use Lorem Ipsum as their default model text, and a search for 'lorem ipsum' will uncover many web sites still in their infancy. Various versions have</p>
      <p class="para closing">The standard chunk of Lorem Ipsum used since the 1500s is reproduced below for those interested. Sections 1.10.32 and 1.10.33 from "de Finibus Bonorum et Malorum" by Cicero are also reproduced in their exact original form, accompanied by English versions from the 1914 translation by H. Rackham.</p>
      <div class="signature" role="img" aria-label="Handwritten signature of the sender"></div>
    </section>
  </main>
</body>
</html>
```